Contemporary new French wine brand needs logo and series of label design

to design a new contemporary logo and series of labels for a new French wine brand. We hope to attract not just current French wine drinkers but new ones who may appreciate a less traditional and more modern style.
Updates

Reason: we are wanting to extend the project for a few days more to receive more submissions since we had fewer designs submitted than we were expecting, maybe because of the holidays.

Target Market(s)

people who follow the arts community (eg. music, theatre, visual/video arts, dance) --- all mature ages.

Industry/Entity Type

French Wine

Requirements
Must have
• a clear, memorable treatment for the name MORIVAL with accompanying logo.
Nice to have
• embossing, matte/gloss refinement, tasteful foil stamping, coated stock for the whites to help the integrity of the paper in and out of ice buckets. A combo of say, three types of fonts; a semi custom font for the brand name Morival and maybe a script and one other.
Should not have
• not traditional French

```html
<!DOCTYPE html>
<html lang="en">
<head>
<meta charset="UTF-8">
<title>Morival – Label Series</title>
<link href="https://fonts.googleapis.com/css2?family=Cinzel:wght@500&family=Libre+Caslon+Text&family=Petit+Formal+Script&display=swap" rel="stylesheet">
<style>
  :root {
    --canvas: #ffffff;
    --rose: #8c1d1c;
    --noir: #1c1c1a;
    --olive: #5f6640;
    --gold-light: #f3d27a;
    --gold-mid: #c98a2e;
    --gold-deep: #8a4b12;
    --ink: #1a1410;
    --wordmark-dark: #2a1c16;
  }
  * { margin: 0; padding: 0; box-sizing: border-box; }
  html, body { width: 1200px; height: 1000px; overflow: hidden; background: var(--canvas); }
  .canvas { position: relative; width: 1200px; height: 1000px; }

  .label { position: absolute; overflow: hidden; }
  .label--rose { left: 62px; top: 493px; width: 203px; height: 287px; background: var(--rose); }
  .label--cabernet { left: 348px; top: 493px; width: 208px; height: 287px; background: var(--noir); }
  .label--blanc { left: 620px; top: 493px; width: 206px; height: 287px; background: var(--olive); }
  .label--feature { left: 870px; top: 292px; width: 290px; height: 406px; background: var(--noir); }

  .label__mark {
    position: absolute; border-radius: 50%;
    border: 4px solid var(--gold-mid);
  }
  .label:not(.label--feature) .label__mark { left: 27px; top: 29px; width: 96px; height: 96px; }
  .label--feature .label__mark { left: 50px; top: 25px; width: 130px; height: 130px; border-width: 5px; }

  .label__wordmark {
    position: absolute; left: 0; right: 0; text-align: center;
    font-family: "Cinzel", serif; font-weight: 500;
    letter-spacing: 0.22em; padding-left: 0.22em;
    color: var(--gold-mid);
  }
  .label:not(.label--feature) .label__wordmark { top: 184px; font-size: 21px; }
  .label--rose .label__wordmark { color: var(--wordmark-dark); }
  .label--feature .label__wordmark { top: 262px; font-size: 31px; }

  .label__band {
    position: absolute; left: 0; right: 0;
    background: linear-gradient(90deg, var(--gold-deep) 0%, var(--gold-mid) 22%, var(--gold-light) 50%, var(--gold-mid) 78%, var(--gold-deep) 100%);
    display: flex; flex-direction: column; align-items: center; justify-content: center;
    color: var(--ink);
  }
  .label:not(.label--feature) .label__band { top: 232px; height: 53px; }
  .label--feature .label__band { top: 328px; height: 78px; }

  .label__variety { font-family: "Libre Caslon Text", serif; line-height: 1; }
  .label:not(.label--feature) .label__variety { font-size: 12px; }
  .label--feature .label__variety { font-size: 18px; }

  .label__region { font-family: "Petit Formal Script", cursive; line-height: 1.2; }
  .label:not(.label--feature) .label__region { font-size: 13px; margin-top: 5px; }
  .label--feature .label__region { font-size: 18px; margin-top: 8px; }
</style>
</head>
<body>
<main class="canvas">
  <section class="label label--rose">
    <div class="label__mark"></div>
    <div class="label__wordmark">MORIVAL</div>
    <div class="label__band">
      <span class="label__variety">ROSE DE PROVENCE</span>
      <span class="label__region">Val de Loire</span>
    </div>
  </section>

  <section class="label label--cabernet">
    <div class="label__mark"></div>
    <div class="label__wordmark">MORIVAL</div>
    <div class="label__band">
      <span class="label__variety">CABERNET SAUVIGNON</span>
      <span class="label__region">Val de Loire</span>
    </div>
  </section>

  <section class="label label--blanc">
    <div class="label__mark"></div>
    <div class="label__wordmark">MORIVAL</div>
    <div class="label__band">
      <span class="label__variety">SAUVIGNON BLANC</span>
      <span class="label__region">Val de Loire</span>
    </div>
  </section>

  <section class="label label--feature">
    <div class="label__mark"></div>
    <div class="label__wordmark">MORIVAL</div>
    <div class="label__band">
      <span class="label__variety">CABERNET SAUVIGNON</span>
      <span class="label__region">Val de Loire</span>
    </div>
  </section>
</main>
</body>
</html>
```